Pellham Grove Trust - New Website Designed

I need a site that looks like this http://www.quorlandgiving.org for boat donations. So please replace the cars with boats.

```html
<!DOCTYPE html>
<html lang="en">
<head>
<meta charset="utf-8">
<title>Pellham Grove Trust – Donate Your Boat</title>
<link href="https://fonts.googleapis.com/css2?family=Roboto+Condensed:wght@400;700&family=Roboto:wght@400;500;700&display=swap" rel="stylesheet">
<style>
:root{
  --navy:#16284a;
  --navy-deep:#0e1a33;
  --nav-blue:#5479bd;
  --red:#c3151b;
  --red-dark:#9c0f13;
  --grey-band:#e6e6e6;
  --ink:#333a44;
  --muted:#6b717a;
  --accent-blue:#4e72b5;
  --acc-head:#6f8ec6;
  --acc-btn:#3b3f45;
  --footer:#4a6db3;
  --white:#ffffff;
}
*{box-sizing:border-box;margin:0;padding:0}
html,body{width:1200px;height:2799px;overflow:hidden}
body{position:relative;background:var(--white);font-family:"Roboto",Arial,sans-serif;color:var(--ink)}
.abs{position:absolute}
.cond{font-family:"Roboto Condensed","Arial Narrow",sans-serif}

/* header */
.site-header{left:0;top:0;width:1200px;height:131px;background:linear-gradient(100deg,#1b2f57 0%,#23407a 35%,#182c52 70%,#101d38 100%)}
.brand{left:97px;top:40px;font-family:"Roboto Condensed",sans-serif;font-weight:700;font-size:36px;color:var(--white);letter-spacing:.5px}
.call{left:690px;top:36px;display:flex;align-items:center;gap:14px;color:var(--white)}
.call-icon{width:40px;height:40px;border:2px solid #fff;border-radius:50%;display:flex;align-items:center;justify-content:center}
.call-text{font-family:"Roboto Condensed",sans-serif;font-size:20px;line-height:24px}
.btn-top{left:963px;top:41px;width:138px;height:34px;background:var(--red);color:#fff;font-size:15px;display:flex;align-items:center;justify-content:center;border-radius:3px}

/* nav */
.main-nav{left:0;top:131px;width:1200px;height:52px;background:var(--nav-blue)}
.main-nav a{position:absolute;top:0;height:52px;line-height:52px;color:#fff;font-size:14px;text-decoration:none;font-family:"Roboto Condensed",sans-serif}
.main-nav .active{background:var(--red);width:101px;text-align:center;left:99px}

/* hero */
.hero{left:0;top:183px;width:1200px;height:479px;background:linear-gradient(180deg,#8a9199 0%,#b8bec3 35%,#6f7a7e 60%,#4c5556 100%)}
.hero-dots{left:561px;top:607px;display:flex;gap:6px}
.hero-dots span{width:12px;height:12px;border-radius:50%;border:2px solid #fff;background:transparent}
.hero-dots span.on{background:var(--red)}

/* donation form */
.donate-form{left:773px;top:112px;width:324px;height:513px;background:var(--red);border-radius:0 0 10px 10px;box-shadow:0 4px 10px rgba(0,0,0,.3)}
.donate-form h2{height:76px;line-height:76px;text-align:center;color:#fff;font-family:"Roboto Condensed",sans-serif;font-weight:400;font-size:21px;border-bottom:1px solid rgba(255,255,255,.2)}
.form-sub{position:absolute;top:96px;width:100%;text-align:center;color:#fff;font-family:"Roboto Condensed",sans-serif;font-weight:700;font-size:14px}
.field{position:absolute;left:24px;width:280px;height:33px;background:#fff;border-radius:2px;font-size:11px;color:#8a8a8a;padding-left:12px;line-height:33px}
.field.half{width:136px}
.field .caret{position:absolute;right:10px;top:0;font-size:9px}
.donate-btn{position:absolute;left:24px;top:444px;width:280px;height:38px;background:var(--accent-blue);color:#fff;text-align:center;line-height:38px;font-family:"Roboto Condensed",sans-serif;font-size:15px;border-radius:2px}

/* promise band */
.promise{left:0;top:662px;width:1200px;height:243px;background:var(--grey-band)}
.promise-arrow{left:0;top:662px}
.promise-title{left:40px;top:717px;width:370px;text-align:center;color:#fff;font-family:"Roboto Condensed",sans-serif}
.promise-title .l1{font-size:25px}
.promise-title .l2{font-size:54px;font-weight:700;line-height:60px;letter-spacing:1px}
.promise-title .l3{font-size:25px}
.feature{top:722px;width:130px;text-align:center;font-size:13px;line-height:18px;color:#3e4550}
.feature svg{display:block;margin:0 auto 14px}

/* section titles */
.sec-title{left:0;width:1200px;text-align:center;font-family:"Roboto Condensed",sans-serif;font-weight:700;font-size:31px;color:#2e333a}
.sec-rule{left:565px;width:70px;height:3px;background:var(--accent-blue)}

/* steps */
.step{top:1105px;width:330px}
.step-pin{position:absolute;left:0;top:0}
.step h3{position:absolute;left:101px;top:0;font-family:"Roboto Condensed",sans-serif;font-weight:400;font-size:18px;line-height:22px;color:var(--red)}
.step p{position:absolute;left:101px;top:58px;width:225px;font-size:12px;line-height:19px;color:var(--muted)}
.step .more{position:absolute;left:101px;top:132px;font-size:11px;color:#444}

/* why */
.why{left:0;top:1331px;width:1200px;height:498px;background:linear-gradient(90deg,#1a1d24 0%,#2a2e38 40%,#5a3436 65%,#1c1f26 100%)}
.why-photo-area{left:620px;top:1331px;width:580px;height:498px;background:radial-gradient(ellipse at 60% 55%,rgba(0,0,0,.75) 0%,rgba(0,0,0,.2) 55%,rgba(0,0,0,0) 80%)}
.why h2{position:absolute;left:99px;top:112px;font-family:"Roboto",sans-serif;font-weight:700;font-size:29px;color:#fff}
.why ul{position:absolute;left:99px;top:174px;list-style:none}
.why li{height:34px;font-size:15px;color:#fff;display:flex;align-items:center;white-space:nowrap}
.why li::before{content:"";width:9px;height:9px;border:2px solid #fff;border-radius:50%;margin-right:10px}
.why li small{font-size:11px;color:#e4e4e4;margin-left:4px}

/* faq */
.faq-photo{left:99px;top:2015px;width:478px;height:316px;background:linear-gradient(180deg,#6a6d66 0%,#4b4e48 50%,#2b2c29 100%)}
.acc{left:620px;width:481px}
.acc-head{height:36px;line-height:36px;padding-left:15px;font-size:14px;position:relative}
.acc-open .acc-head{background:var(--acc-head);color:#fff}
.acc-closed{border:1px solid #dcdcdc}
.acc-closed .acc-head{height:34px;line-height:34px;color:#555;background:#f8f8f8}
.acc-btn{position:absolute;right:0;top:0;width:34px;height:100%;background:var(--acc-btn);color:#fff;text-align:center;font-size:20px}
.acc-body{border:1px solid #dcdcdc;border-top:none;padding:18px 15px 16px;font-size:11.5px;line-height:19px;color:#555;height:97px}

/* footer */
.site-footer{left:0;top:2431px;width:1200px;height:368px;background:linear-gradient(120deg,#4467ad 0%,#5277bd 50%,#4567ab 100%);color:#fff}
.site-footer h4{position:absolute;top:54px;font-family:"Roboto Condensed",sans-serif;font-weight:400;font-size:18px}
.foot-line{position:absolute;font-size:13px;line-height:18px;display:flex;align-items:flex-start;gap:14px}
.quick{position:absolute;left:433px;top:101px;list-style:none;font-size:12px;line-height:24.5px}
.social{position:absolute;left:625px;top:99px;list-style:none;font-size:13px}
.social li{display:flex;align-items:center;gap:12px;height:36px}
.social li span.dot{width:26px;height:26px;border:1px solid #fff;border-radius:50%}
.signup-text{position:absolute;left:817px;top:98px;width:285px;font-size:11.5px;line-height:18px}
.signup-input{position:absolute;left:817px;top:146px;width:285px;height:40px;background:#fff;color:#666;font-size:11px;line-height:40px;padding-left:14px}
.signup-btn{position:absolute;left:817px;top:200px;width:113px;height:38px;background:var(--red);font-family:"Roboto Condensed",sans-serif;font-weight:700;font-size:14px;line-height:38px;text-align:center}
.foot-rule{position:absolute;left:0;top:293px;width:1200px;height:1px;background:rgba(255,255,255,.3)}
.copyright{position:absolute;left:0;top:318px;width:1200px;text-align:center;font-size:12px}
</style>
</head>
<body>

<header class="abs site-header">
  <div class="abs brand">PELLHAM GROVE TRUST</div>
  <div class="abs call">
    <div class="call-icon">
      <svg width="20" height="20" viewBox="0 0 24 24"><path d="M6.6 10.8a15.1 15.1 0 0 0 6.6 6.6l2.2-2.2c.3-.3.7-.4 1-.2 1.1.4 2.3.6 3.6.6.6 0 1 .4 1 1V20c0 .6-.4 1-1 1C10.6 21 3 13.4 3 4c0-.6.4-1 1-1h3.5c.6 0 1 .4 1 1 0 1.3.2 2.5.6 3.6.1.3 0 .7-.2 1z" fill="#fff"/></svg>
    </div>
    <div class="call-text">CALL TODAY TO DONATE<br>1-800-555-0147</div>
  </div>
  <div class="abs btn-top">Donate Now</div>
</header>

<nav class="abs main-nav">
  <a class="active" href="#">HOME</a>
  <a href="#" style="left:241px">HOW TO DONATE</a>
  <a href="#" style="left:407px">WHY DONATE</a>
  <a href="#" style="left:550px">FAQ</a>
  <a href="#" style="left:636px">ABOUT</a>
</nav>

<div class="abs hero" role="img" aria-label="Photo of a uniformed soldier embracing his daughter beside a white motorboat on a mountain lake"></div>
<div class="abs hero-dots"><span class="on"></span><span></span><span></span><span></span></div>

<form class="abs donate-form">
  <h2>DONATE YOUR BOAT ONLINE</h2>
  <div class="form-sub">Full Tax Deduction - Running or Not</div>
  <div class="field" style="top:132px">FirstName</div>
  <div class="field" style="top:175px">LastName</div>
  <div class="field" style="top:218px">ZIPCode</div>
  <div class="field" style="top:261px">DayPhone</div>
  <div class="field" style="top:304px">Email</div>
  <div class="field half" style="top:351px">Choose Year<span class="caret">&#9650;&#9660;</span></div>
  <div class="field half" style="top:351px;left:168px">Choose Make<span class="caret">&#9650;&#9660;</span></div>
  <div class="field" style="top:396px">Model of Boat</div>
  <div class="donate-btn">DONATE NOW</div>
</form>

<section>
  <div class="abs promise"></div>
  <svg class="abs promise-arrow" width="450" height="243" viewBox="0 0 450 243"><polygon points="0,0 380,0 448,121 380,243 0,243" fill="#b5141a"/><polygon points="0,0 380,0 448,121 430,121 365,12 0,12" fill="#d02026" opacity=".4"/></svg>
  <div class="abs promise-title">
    <div class="l1">DONATE YOUR BOAT TO</div>
    <div class="l2">VETERANS</div>
    <div class="l3">MAKE A DIFFERENCE</div>
  </div>
  <div class="abs feature" style="left:452px">
    <svg width="52" height="52" viewBox="0 0 52 52"><rect x="6" y="10" width="34" height="34" rx="3" fill="none" stroke="#1f3f7a" stroke-width="4"/><path d="M14 26l9 9 22-24" fill="none" stroke="#1f3f7a" stroke-width="5"/></svg>
    You have<br>no costs</div>
  <div class="abs feature" style="left:566px">
    <svg width="60" height="52" viewBox="0 0 60 52"><rect x="6" y="24" width="40" height="12" fill="none" stroke="#1f3f7a" stroke-width="3"/><rect x="20" y="12" width="14" height="12" fill="none" stroke="#1f3f7a" stroke-width="3"/><path d="M46 30l10-10" stroke="#1f3f7a" stroke-width="3"/><circle cx="15" cy="40" r="5" fill="#1f3f7a"/><circle cx="37" cy="40" r="5" fill="#1f3f7a"/></svg>
    Free towing,<br>running or not</div>
  <div class="abs feature" style="left:693px">
    <svg width="52" height="52" viewBox="0 0 52 52"><path d="M12 4h22l8 8v36H12z" fill="none" stroke="#1f3f7a" stroke-width="3"/><text x="27" y="22" font-size="10" font-family="Arial" font-weight="700" fill="#1f3f7a" text-anchor="middle">TAX</text><path d="M18 30h16M18 36h16M18 42h10" stroke="#1f3f7a" stroke-width="2"/></svg>
    We issue you an<br>IRS tax receipt</div>
  <div class="abs feature" style="left:833px">
    <svg width="56" height="52" viewBox="0 0 56 52"><rect x="6" y="6" width="26" height="34" fill="none" stroke="#1f3f7a" stroke-width="3"/><rect x="18" y="12" width="26" height="34" fill="#fff" stroke="#1f3f7a" stroke-width="3"/><circle cx="36" cy="32" r="8" fill="none" stroke="#1f3f7a" stroke-width="3"/><path d="M42 38l8 8" stroke="#1f3f7a" stroke-width="4"/></svg>
    We take care of<br>all paperwork</div>
  <div class="abs feature" style="left:975px">
    <svg width="52" height="52" viewBox="0 0 52 52"><rect x="10" y="6" width="30" height="40" fill="none" stroke="#1f3f7a" stroke-width="3"/><rect x="18" y="2" width="14" height="8" fill="#1f3f7a"/><path d="M16 18h18M16 25h18M16 32h10" stroke="#1f3f7a" stroke-width="2"/><circle cx="38" cy="38" r="10" fill="#1f3f7a"/><path d="M33 38l4 4 7-7" fill="none" stroke="#fff" stroke-width="2.5"/></svg>
    We take care of<br>DMV &amp; Smog issues</div>
</section>

<section>
  <h2 class="abs sec-title" style="top:983px">HOW TO DONATE</h2>
  <div class="abs sec-rule" style="top:1040px"></div>

  <div class="abs step" style="left:99px">
    <svg class="step-pin" width="84" height="96" viewBox="0 0 84 96"><path d="M42 2a40 40 0 0 1 40 40c0 24-40 52-40 52S2 66 2 42A40 40 0 0 1 42 2z" fill="#5377ba"/><circle cx="42" cy="42" r="32" fill="none" stroke="#fff" stroke-width="1.5" opacity=".6"/><path d="M30 26h18l6 6v24H30z" fill="none" stroke="#fff" stroke-width="2.5"/><path d="M35 38h14M35 44h14M35 50h8" stroke="#fff" stroke-width="2"/></svg>
    <h3>FILL OUT<br>THE ONLINE FORM</h3>
    <p>Share a few details about your boat and we will call you back to arrange pickup.</p>
    <div class="more">READ MORE &#10141;</div>
  </div>

  <div class="abs step" style="left:442px">
    <svg class="step-pin" width="84" height="96" viewBox="0 0 84 96"><path d="M42 2a40 40 0 0 1 40 40c0 24-40 52-40 52S2 66 2 42A40 40 0 0 1 42 2z" fill="#5377ba"/><circle cx="42" cy="42" r="32" fill="none" stroke="#fff" stroke-width="1.5" opacity=".6"/><path d="M22 44h40l-6 8H28z" fill="none" stroke="#fff" stroke-width="2.5"/><path d="M32 44v-8h16l6 8" fill="none" stroke="#fff" stroke-width="2.5"/></svg>
    <h3>WE TOW<br>THE VEHICLE</h3>
    <p>Our local partner tows your boat free of charge, whether it runs or not at all.</p>
    <div class="more">READ MORE &#10141;</div>
  </div>

  <div class="abs step" style="left:802px">
    <svg class="step-pin" width="84" height="96" viewBox="0 0 84 96"><path d="M42 2a40 40 0 0 1 40 40c0 24-40 52-40 52S2 66 2 42A40 40 0 0 1 42 2z" fill="#5377ba"/><circle cx="42" cy="42" r="32" fill="none" stroke="#fff" stroke-width="1.5" opacity=".6"/><path d="M30 24h18l6 6v26H30z" fill="none" stroke="#fff" stroke-width="2.5"/><text x="42" y="40" font-size="8" font-family="Arial" font-weight="700" fill="#fff" text-anchor="middle">TAX</text><path d="M35 46h14M35 51h10" stroke="#fff" stroke-width="2"/></svg>
    <h3>TAX<br>WRITE-OFF</h3>
    <p>After the sale we mail a receipt you can use to claim your tax deduction.</p>
    <div class="more">READ MORE &#10141;</div>
  </div>
</section>

<section class="abs why">
  <h2>WHY DONATE YOUR BOAT TO US?</h2>
  <ul>
    <li>IRS 501(c)3 Approved:<small>Your gift is fully recognized as a charitable donation by the IRS.</small></li>
    <li>Free Local Towing to You:<small>Our crews come to your dock, marina or driveway at no cost.</small></li>
    <li>All Boats Accepted:<small>Sail, power, fishing and pontoon boats of any age are welcome.</small></li>
    <li>Income Tax Deduction:<small>Claim the sale value of your boat on your next federal tax return.</small></li>
    <li>No Paperwork Hassles:<small>We handle titles, transfers and every form so you never have to worry.</small></li>
    <li>Boat donations help fund programs:<small>Proceeds support housing, training and care for veterans and their families.</small></li>
    <li>Schedule a Free Pickup:<small>Choose a pickup time that suits you and we will be there.</small></li>
  </ul>
</section>
<div class="abs why-photo-area" role="img" aria-label="Silhouette of a soldier with a backpack handing a flower to a small girl in front of a flag"></div>

<section>
  <h2 class="abs sec-title" style="top:1902px">FREQUENTLY ASKED QUESTIONS</h2>
  <div class="abs sec-rule" style="top:1967px"></div>
  <div class="abs faq-photo" role="img" aria-label="Photo of rows of soldiers in camouflage uniforms and boots marching"></div>

  <div class="abs acc acc-open" style="top:2019px">
    <div class="acc-head">Why do we use it?<span class="acc-btn">&minus;</span></div>
    <div class="acc-body">Donated boats are sold at auction and the proceeds go straight to veteran programs. Most pickups happen within a week, and you receive your tax receipt by mail soon after the sale.</div>
  </div>
  <div class="abs acc acc-closed" style="top:2165px"><div class="acc-head">Where can I get some?<span class="acc-btn">+</span></div></div>
  <div class="abs acc acc-closed" style="top:2208px"><div class="acc-head">Where does it come from?<span class="acc-btn">+</span></div></div>
  <div class="abs acc acc-closed" style="top:2251px"><div class="acc-head">Where can I get some?<span class="acc-btn">+</span></div></div>
  <div class="abs acc acc-closed" style="top:2294px"><div class="acc-head">Where does it come from?<span class="acc-btn">+</span></div></div>
</section>

<footer class="abs site-footer">
  <h4 style="left:99px">CONTACT US</h4>
  <div class="foot-line" style="left:99px;top:100px">
    <svg width="14" height="18" viewBox="0 0 14 18"><path d="M7 1a6 6 0 0 1 6 6c0 4-6 10-6 10S1 11 1 7a6 6 0 0 1 6-6z" fill="none" stroke="#fff" stroke-width="1.5"/><circle cx="7" cy="7" r="2" fill="#fff"/></svg>
    <span>Pellham Grove Trust<br>Ashdown Lane, Fernley, Harts</span></div>
  <div class="foot-line" style="left:99px;top:154px">
    <svg width="16" height="16" viewBox="0 0 24 24"><path d="M6.6 10.8a15.1 15.1 0 0 0 6.6 6.6l2.2-2.2c.3-.3.7-.4 1-.2 1.1.4 2.3.6 3.6.6.6 0 1 .4 1 1V20c0 .6-.4 1-1 1C10.6 21 3 13.4 3 4c0-.6.4-1 1-1h3.5c.6 0 1 .4 1 1 0 1.3.2 2.5.6 3.6.1.3 0 .7-.2 1z" fill="#fff"/></svg>
    <span>Phone : +44(0)20 5550 1182</span></div>
  <div class="foot-line" style="left:99px;top:188px">
    <svg width="16" height="14" viewBox="0 0 16 14"><rect x="1" y="1" width="14" height="12" fill="none" stroke="#fff" stroke-width="1.5"/><path d="M1 1l7 6 7-6" fill="none" stroke="#fff" stroke-width="1.5"/></svg>
    <span>Email: info@pellhamgrovetrust.org</span></div>

  <h4 style="left:433px">QUICK LINKS</h4>
  <ul class="quick"><li>Home</li><li>About Us</li><li>How To Donate</li><li>Why Donate</li><li>Blog</li><li>Contact Us</li></ul>

  <h4 style="left:625px">SOCIAL</h4>
  <ul class="social">
    <li><span class="dot"></span>Harborfeed</li>
    <li><span class="dot"></span>Chirpline</li>
    <li><span class="dot"></span>Circleplus</li>
    <li><span class="dot"></span>Reelstream</li>
  </ul>

  <h4 style="left:817px">SIGN UP TO RECEIVE EMAIL</h4>
  <p class="signup-text">Get news on our programs, veteran stories and ways to give, straight to your inbox.</p>
  <div class="signup-input">Enter Name</div>
  <div class="signup-btn">SUBSCRIBE</div>

  <div class="foot-rule"></div>
  <div class="copyright">Copyright © Pellham Grove Trust 2017. All rights reserved.</div>
</footer>

</body>
</html>
```